App Design - Career Prep Pal

We require an App Design for our new App called 'Hiring Helper'. This app is essentially an assistant to help Users prepare for job interviews, to help them get hired. <br/><br/>Users who download the App can view common Questions and Answers, save their favourite responses and also view common Interview Tips. <br/><br/>The vision for our App is for Users who are preparing for an interview (1 week before, 1 day before, even 1 hour before), are able to download, view and educate themselves on common questions and responses, and then be confident to land the job. <br/><br/>Our team has developed wireframes to help highlight what each screen should do and include. Please see attached document, which also highlights key requirements for the experience. Feel free to add/remove/edit what you see on these wireframes. Our preference is that you use Adobe XD please.<br/><br/>In terms of design guidelines, we want the experience to be simple, intuitive and 'memorable' to help Users to remember the questions/responses when they are in the interview. <br/><br/>The final design should communicate 'neat and clean professionalism'; we like the design of: jobvista net au<br/><br/>Thank you for reading! Good luck !

Target Market(s)

Professional job seekers

Font styles to use
Sans Serif

Colors

Designer to choose colors to be used in the design.

Requirements
Must have
• Please see my PixelGuild_UX file that I have uploaded
Nice to have
• Could you also please include some ideas on how we can incorporate Advertising into the app screens

```html
<!DOCTYPE html>
<html lang="en">
<head>
<meta charset="utf-8">
<title>Hiring Helper – App Screens</title>
<link href="https://fonts.googleapis.com/css2?family=Catamaran:wght@400;500;600;700&display=swap" rel="stylesheet">
<style>
:root{
  --page:#f2f2f2;
  --blue:#0a5ff0;
  --blue-deep:#0047e0;
  --blue-light:#1a7cff;
  --ink:#1c2a45;
  --muted:#5a6070;
  --surface:#f1f2f7;
  --card:#ffffff;
  --white:#ffffff;
}
*{box-sizing:border-box;margin:0;padding:0}
html,body{width:1200px;height:566px;overflow:hidden;background:var(--page);font-family:'Catamaran',sans-serif}
.screen{position:absolute;top:34px;width:227px;height:468px;border-radius:28px;overflow:hidden;background:var(--surface)}
.screen--splash{left:60px}
.screen--menu{left:347px}
.screen--categories{left:632px}
.screen--list{left:904px}

.splash-bg{position:absolute;inset:0;background:linear-gradient(170deg,#0650e6 0%,#0a62f2 55%,#0b78ff 100%)}
.header{position:absolute;left:0;top:0;width:100%}
.header svg{display:block}
.app-mark{position:absolute;left:50%;transform:translateX(-50%);width:33px;height:33px;border-radius:50%;background:var(--white)}
.app-name{position:absolute;left:0;width:100%;text-align:center;color:var(--white);font-weight:500;letter-spacing:.2px}
.subtitle{position:absolute;left:0;width:100%;text-align:center;color:var(--white);font-size:13.5px;font-weight:500}
.tagline{position:absolute;left:16px;right:16px;top:202px;text-align:center;color:var(--white);font-size:19px;font-weight:700;line-height:24.5px}

.menu-btn{position:absolute;left:19px;width:195px;height:37px;background:var(--card);box-shadow:0 2px 6px rgba(20,40,90,.08);display:flex;align-items:center;padding-left:14px;gap:9px;color:var(--blue);font-weight:700;font-size:11.5px}
.menu-btn svg{flex:none}

.section-title{position:absolute;left:0;width:100%;text-align:center;color:var(--ink);font-size:13px;font-weight:500}
.category{position:absolute;left:18px;width:192px;height:40px;display:flex;align-items:center;justify-content:center;color:var(--white);font-weight:700;font-size:11px;letter-spacing:.2px}
.category--behavioural{top:199px;background:linear-gradient(90deg,#2f9a2a,#58c44a 50%,#2a8f26)}
.category--situational{top:250px;background:linear-gradient(90deg,#ff6a00,#ff4a10 60%,#e8261a)}
.category--motivational{top:302px;background:linear-gradient(90deg,#5530d8,#4a2bc9 55%,#2c1fb0)}
.category--technical{top:353px;background:linear-gradient(90deg,#0d5cf0,#1570ff 60%,#0b49e6)}
.view-all{position:absolute;left:71px;top:412px;width:85px;height:23px;border:1px solid var(--blue);background:var(--white);color:var(--blue);font-weight:700;font-size:9.5px;display:flex;align-items:center;justify-content:center}

.question{position:absolute;left:29px;width:180px;background:var(--card);padding:11px 8px 0 21px;color:var(--muted);font-size:6.3px;line-height:10px}
.question-num{position:absolute;left:17px;width:22px;height:22px;border-radius:50%;background:var(--blue);color:var(--white);font-size:9.5px;font-weight:600;display:flex;align-items:center;justify-content:center}
</style>
</head>
<body>

<!-- Splash -->
<section class="screen screen--splash">
  <div class="splash-bg" role="img" aria-label="Blue-tinted photo of a job interview at a desk"></div>
  <div class="app-mark" style="top:50px;width:43px;height:43px"></div>
  <h1 class="app-name" style="top:96px;font-size:25px">Hiring Helper</h1>
  <p class="tagline">Your guide to the Most common interview questions, and the best responses to help you get hired.</p>
</section>

<!-- Main menu -->
<section class="screen screen--menu">
  <div class="header">
    <svg width="227" height="150" viewBox="0 0 227 150">
      <defs><linearGradient id="hdr1" x1="0" y1="0" x2="0" y2="1"><stop offset="0" stop-color="#0654ea"/><stop offset="1" stop-color="#0b6dff"/></linearGradient></defs>
      <path d="M0 0H227V128C205 118 190 122 170 128C140 136 120 112 90 118C60 124 40 140 0 132Z" fill="url(#hdr1)"/>
      <path d="M0 132C30 124 50 128 70 134C55 128 30 124 0 136Z M140 128C165 122 190 134 227 128V132C195 138 170 126 140 128Z" fill="#6fa8ff" opacity=".7"/>
    </svg>
  </div>
  <div class="app-mark" style="top:38px"></div>
  <h1 class="app-name" style="top:73px;font-size:19.5px">Hiring Helper</h1>
  <div class="menu-btn" style="top:190px">
    <svg width="22" height="22" viewBox="0 0 22 22" fill="none" stroke="#0a5ff0" stroke-width="1.2"><circle cx="9" cy="8" r="5"/><path d="M9 13v3h3M14 11l3 2-2 1v4h-5"/></svg>
    View Question &amp; Response</div>
  <div class="menu-btn" style="top:242px">
    <svg width="22" height="22" viewBox="0 0 22 22" fill="none" stroke="#0a5ff0" stroke-width="1.2"><rect x="2" y="8" width="11" height="9" rx="2"/><circle cx="15" cy="7" r="5"/><path d="M13.5 5.5a1.5 1.5 0 1 1 1.5 2v1M15 10v.3"/></svg>
    My Question Portfolio</div>
  <div class="menu-btn" style="top:295px">
    <svg width="22" height="22" viewBox="0 0 22 22" fill="none" stroke="#0a5ff0" stroke-width="1.2"><rect x="4" y="4" width="14" height="12" rx="3"/><path d="M9 16l-2 4 4-4M11 7v4M11 13v.3"/></svg>
    Interview Tips</div>
</section>

<!-- Categories -->
<section class="screen screen--categories">
  <div class="header">
    <svg width="227" height="160" viewBox="0 0 227 160">
      <defs><linearGradient id="hdr2" x1="0" y1="0" x2="0" y2="1"><stop offset="0" stop-color="#0654ea"/><stop offset="1" stop-color="#0b6dff"/></linearGradient></defs>
      <path d="M0 0H227V136C205 126 190 130 170 136C140 144 120 120 90 126C60 132 40 148 0 140Z" fill="url(#hdr2)"/>
      <path d="M0 140C30 132 50 136 70 142C55 136 30 132 0 144Z M140 136C165 130 190 142 227 136V140C195 146 170 134 140 136Z" fill="#6fa8ff" opacity=".7"/>
    </svg>
  </div>
  <div class="app-mark" style="top:26px"></div>
  <h1 class="app-name" style="top:61px;font-size:19.5px">Hiring Helper</h1>
  <p class="subtitle" style="top:93px">View Question &amp; Response</p>
  <h2 class="section-title" style="top:160px">Select your question category</h2>
  <div class="category category--behavioural" role="img" aria-label="Green maze photo behind the Behavioural category">Behaviroural</div>
  <div class="category category--situational" role="img" aria-label="Orange leaf photo behind the Situational category">Situational</div>
  <div class="category category--motivational" role="img" aria-label="Purple mountain photo behind the Motivational category">Motivational</div>
  <div class="category category--technical" role="img" aria-label="Blue network graphic behind the Technical category">Technical</div>
  <div class="view-all">View All</div>
</section>

<!-- Question list -->
<section class="screen screen--list">
  <div class="header">
    <svg width="227" height="160" viewBox="0 0 227 160">
      <defs><linearGradient id="hdr3" x1="0" y1="0" x2="0" y2="1"><stop offset="0" stop-color="#0654ea"/><stop offset="1" stop-color="#0b6dff"/></linearGradient></defs>
      <path d="M0 0H227V128C205 118 190 122 170 128C140 136 120 112 90 118C60 124 40 140 0 132Z" fill="url(#hdr3)"/>
      <path d="M0 132C30 124 50 128 70 134C55 128 30 124 0 136Z M140 128C165 122 190 134 227 128V132C195 138 170 126 140 128Z" fill="#6fa8ff" opacity=".7"/>
    </svg>
  </div>
  <div class="app-mark" style="top:26px"></div>
  <h1 class="app-name" style="top:61px;font-size:19.5px">Hiring Helper</h1>
  <p class="subtitle" style="top:93px">View Question &amp; Response</p>
  <h2 class="section-title" style="top:152px;font-size:13.5px">Behavioural</h2>

  <div class="question" style="top:177px;height:49px">Tell me about a time you handled a difficult conflict with a coworker</div>
  <div class="question-num" style="top:190px">1</div>
  <div class="question" style="top:234px;height:49px">Describe a situation where you missed a deadline and explain what you learned from it</div>
  <div class="question-num" style="top:247px">2</div>
  <div class="question" style="top:290px;height:44px">Give an example of a goal you reached and how</div>
  <div class="question-num" style="top:300px">3</div>
  <div class="question" style="top:342px;height:44px">Share a time you showed leadership without a formal title</div>
  <div class="question-num" style="top:352px">4</div>
  <div class="question" style="top:394px;height:44px">Describe how you adapted to a major change at work</div>
  <div class="question-num" style="top:404px">5</div>
</section>

</body>
</html>
```